Website Design for a holiday home letting busines

We require a redesign of our present website www.pinebrookstays.com. We want the website to stand out and look professional and clean to make holiday hunters want to book a caravan or lodge holiday with us. Our logo is red however we DO NOT want the website to be red. We want a natural colour scheme.

The final design should communicate that we are a professional company to book with.

On the home page we require;
Overview of company
Photo
Search box for holiday (check in)
Late Deals
Reviews
News

We would like the following pages designed; home page, available dates page, caravans page, content page.

The website should be responsive for smart phones. One website I do like is http://www.verdoliso.be/nl/

Target Market(s)

Families

Industry/Entity Type

Travel

Number of Pages Required

5+ page

Font styles to use
Serif

Requirements
Must have
• The project must be responsive for mobile phones and tablets.
• Ability to search for holiday home holidays
• We want a natural colour scheme.
Nice to have
• A style we like is http://www.verdoliso.be/nl/
Should not have
• Do not use red as a colour for the website. Our logo is red so this is the only time we want this used.

```html
<!DOCTYPE html>
<html lang="en">
<head>
<meta charset="utf-8">
<title>Pinebrook Stays – Caravan &amp; Lodge Holidays</title>
<link rel="stylesheet" href="https://fonts.googleapis.com/css2?family=Lora:wght@400;600;700&family=Open+Sans:wght@400;600;700&display=swap">
<style>
:root{
  --pine:#4f7a5a;
  --pine-dark:#3c6046;
  --bark:#6e5a45;
  --ink:#35322e;
  --muted:#8a847c;
  --line:#e4e0d8;
  --soft:#f3f1ec;
  --footer:#2f2b27;
  --footer-deep:#24211e;
  --brand:#c8322d;
  --star:#c99a2e;
  --white:#fff;
}
*{box-sizing:border-box;margin:0;padding:0}
html,body{width:1200px;height:2540px;overflow:hidden}
body{font-family:"Open Sans",Arial,sans-serif;color:var(--ink);background:var(--white);font-size:13px}
h1,h2,h3,h4,h5,.serif{font-family:"Lora",Georgia,serif}
.wrap{width:1080px;margin:0 auto;position:relative}

/* header */
.topbar{height:120px}
.topbar .wrap{display:flex;align-items:center;height:120px;justify-content:space-between}
.brand{display:flex;align-items:center;gap:10px}
.brand-mark{width:32px;height:32px;border-radius:50%;background:var(--brand)}
.brand-name{font-family:"Lora",Georgia,serif;font-size:26px;font-weight:700;color:var(--brand);line-height:1.1}
.brand-tag{font-size:10px;color:var(--muted);margin-top:2px}
.contact-line{display:flex;align-items:center;gap:28px;font-size:13px;color:var(--muted)}
.contact-line span{display:flex;align-items:center;gap:7px}
.btn{background:var(--pine);color:var(--white);font-weight:700;font-size:12px;padding:9px 16px;border-radius:3px;text-transform:uppercase}

.nav{height:44px;border-top:1px solid var(--line)}
.nav ul{list-style:none;display:flex;height:44px;width:1080px;margin:0 auto}
.nav li{padding:0 15px;line-height:44px;font-size:11px;font-weight:600;text-transform:uppercase;color:#5f5a53}
.nav li.active{background:var(--pine);color:var(--white)}

.hero{height:456px;background:linear-gradient(110deg,#6b5a4c 0%,#b9a58f 35%,#ddd4c8 60%,#9fb2a8 100%);position:relative}
.dots{position:absolute;bottom:16px;left:0;right:0;display:flex;justify-content:center;gap:8px}
.dots i{width:9px;height:9px;border-radius:50%;background:rgba(255,255,255,.6)}
.dots i.on{background:var(--pine)}

/* headings */
.section-title{text-align:center;font-size:22px;font-weight:600;text-transform:uppercase;color:var(--ink);letter-spacing:.5px}
.section-title b{color:var(--pine);font-weight:600}
.section-title::after{content:"";display:block;width:44px;height:2px;background:var(--pine);margin:10px auto 0}

.welcome{height:200px;padding-top:44px;text-align:center}
.welcome p{width:820px;margin:22px auto 0;color:var(--muted);line-height:1.7;font-size:13px}

.listing{background:var(--soft);height:460px;padding-top:36px}
.cards{display:flex;gap:18px;margin-top:30px}
.card{flex:1;background:var(--white);border:1px solid var(--line);padding:10px}
.card .photo{height:140px;background:linear-gradient(135deg,#8c7560,#cdbba5 60%,#e9e2d6)}
.card h3{color:var(--pine);font-size:13px;font-weight:700;margin:12px 0 8px;text-transform:uppercase}
.card dl{display:grid;grid-template-columns:1fr 1fr;gap:5px 6px;font-size:10px;text-transform:uppercase}
.card dt{color:var(--muted)}
.card dd{font-weight:700}
.card .more{display:flex;justify-content:space-between;align-items:center;margin-top:10px;padding-top:8px;border-top:1px solid var(--line);font-size:10px;color:var(--muted)}
.card .more em{font-style:normal;background:var(--pine);color:var(--white);padding:3px 8px;border-radius:2px}

.search{background:var(--pine);height:200px;padding-top:50px}
.search .section-title{color:var(--white)}
.search .section-title::after{background:var(--white)}
.search-row{display:flex;gap:10px;margin-top:24px}
.field{flex:1;height:36px;background:var(--white);border-radius:2px;font-size:11px;color:var(--muted);display:flex;align-items:center;padding:0 12px;justify-content:space-between}
.field.wide{flex:1.8}
.search-row .go{background:var(--footer);color:var(--white);font-weight:700;font-size:12px;padding:0 28px;display:flex;align-items:center;border-radius:2px}

.deals{height:420px;padding-top:40px}

/* bottom content */
.feeds{border-top:1px solid var(--line);padding-top:40px;height:460px}
.feeds .wrap{display:flex;gap:44px}
.col{flex:1}
.col h4{font-size:18px;font-weight:600;padding-bottom:10px;border-bottom:1px solid var(--line);margin-bottom:16px}
.item{margin-bottom:22px}
.item .who{color:var(--pine);font-size:11px;font-weight:700;text-transform:uppercase}
.item .who span{color:var(--muted);font-weight:400;text-transform:none}
.item p{font-size:11px;color:var(--muted);line-height:1.6;margin-top:6px}
.stars{color:var(--star);font-size:11px;letter-spacing:1px}
.item .date{font-size:10px;color:var(--muted);margin-top:6px}
.social{flex:0 0 290px;border:1px solid var(--line);align-self:flex-start}
.social header{background:var(--pine-dark);color:var(--white);font-family:"Lora",Georgia,serif;font-size:14px;font-weight:600;padding:9px 12px}
.social .sub{font-size:11px;font-weight:700;padding:8px 12px;border-bottom:1px solid var(--line)}
.social li{list-style:none;display:flex;gap:8px;padding:8px 12px;font-size:10px;color:var(--muted);border-bottom:1px solid var(--line)}
.social li:last-child{border-bottom:0}
.social li i{flex:0 0 28px;height:28px;background:#d8d3ca}
.social li b{color:var(--pine-dark)}

/* footer */
.footer{background:var(--footer);color:#bdb6ab;height:150px;padding-top:22px}
.footer .wrap{display:flex;gap:40px}
.footer .fcol{flex:1;font-size:11px;line-height:1.7}
.footer .fcol.first{flex:1.6}
.footer h5{color:var(--white);font-size:12px;font-weight:700;text-transform:uppercase;margin-bottom:8px;letter-spacing:.5px}
.footer .input{height:26px;background:var(--white);border-radius:2px;margin:6px 0 8px;padding:0 10px;line-height:26px;color:var(--muted);width:240px}
.footer .btn{display:inline-block;padding:5px 14px;font-size:11px}
.footer .circle{display:flex;align-items:center;gap:8px;margin-bottom:3px}
.footer .circle i{width:18px;height:18px;border-radius:50%;background:#57514a}
.copy{background:var(--footer-deep);height:30px;color:#8c857b;font-size:10px;text-align:center;line-height:30px}
</style>
</head>
<body>

<header class="topbar">
  <div class="wrap">
    <div class="brand"><span class="brand-mark"></span><div><div class="brand-name">Pinebrook Stays</div><div class="brand-tag">Caravan &amp; lodge holiday hire</div></div></div>
    <div class="contact-line">
      <span><svg width="14" height="14" viewBox="0 0 24 24"><path fill="#4f7a5a" d="M6.6 10.8a15 15 0 0 0 6.6 6.6l2.2-2.2c.3-.3.7-.4 1-.2 1.1.4 2.3.6 3.6.6.6 0 1 .4 1 1V20c0 .6-.4 1-1 1A17 17 0 0 1 3 4c0-.6.4-1 1-1h3.5c.6 0 1 .4 1 1 0 1.3.2 2.5.6 3.6.1.3 0 .7-.2 1z"/></svg>+44 1632 960 418</span>
      <span><svg width="15" height="12" viewBox="0 0 24 18"><rect x="1" y="1" width="22" height="16" fill="none" stroke="#4f7a5a" stroke-width="2"/><path d="M1 1l11 9 11-9" fill="none" stroke="#4f7a5a" stroke-width="2"/></svg>hello@pinebrookstays.com</span>
      <span class="btn">Live chat</span>
    </div>
  </div>
</header>

<nav class="nav">
  <ul>
    <li class="active">Home</li><li>News</li><li>Reviews</li><li>Caravans &amp; Lodges</li><li>Site Facilities</li><li>Our Holidays</li><li>Payment Info</li><li>Availability Dates</li><li>Local Attractions</li><li>Contact Us</li>
  </ul>
</nav>

<section class="hero" role="img" aria-label="Bright lodge living room with stone fireplace, sofas and large windows">
  <div class="dots"><i class="on"></i><i></i><i></i></div>
</section>

<section class="welcome">
  <h2 class="section-title">Welcome to <b>Pinebrook Stays</b></h2>
  <p>We have flexible low cost weekly and monthly payment plans available and our lodges are set in quiet woodland so every family can relax and enjoy its holiday. This means you can secure your holiday now without making a large payment, with all facilities open from spring until late autumn.</p>
</section>

<section class="listing">
  <div class="wrap">
    <h2 class="section-title">List of <b>Caravans and Lodges</b></h2>
    <div class="cards">
      <article class="card"><div class="photo" role="img" aria-label="Caravan lounge interior"></div><h3>The Birchwood</h3><dl><dt>Caravan type</dt><dd>Lodge</dd><dt>Sleeps</dt><dd>6</dd></dl><div class="more">From £250<em>More info</em></div></article>
      <article class="card"><div class="photo" role="img" aria-label="Lodge kitchen and dining area"></div><h3>The Alder</h3><dl><dt>Caravan type</dt><dd>Lodge</dd><dt>Sleeps</dt><dd>4</dd></dl><div class="more">From £220<em>More info</em></div></article>
      <article class="card"><div class="photo" role="img" aria-label="Caravan bedroom"></div><h3>The Rowan</h3><dl><dt>Caravan type</dt><dd>Caravan</dd><dt>Sleeps</dt><dd>6</dd></dl><div class="more">From £190<em>More info</em></div></article>
      <article class="card"><div class="photo" role="img" aria-label="Lodge lounge with sofas"></div><h3>The Hazel</h3><dl><dt>Caravan type</dt><dd>Lodge</dd><dt>Sleeps</dt><dd>8</dd></dl><div class="more">From £310<em>More info</em></div></article>
      <article class="card"><div class="photo" role="img" aria-label="Caravan living room"></div><h3>The Larch</h3><dl><dt>Caravan type</dt><dd>Lodge</dd><dt>Sleeps</dt><dd>6</dd></dl><div class="more">From £250<em>More info</em></div></article>
    </div>
  </div>
</section>

<section class="search">
  <div class="wrap">
    <h2 class="section-title">Search Function</h2>
    <div class="search-row">
      <div class="field wide">Search the property</div>
      <div class="field">Check in date <span>▾</span></div>
      <div class="field">Check out date <span>▾</span></div>
      <div class="field">Display price <span>▾</span></div>
      <div class="go">BOOK NOW</div>
    </div>
  </div>
</section>

<section class="deals">
  <div class="wrap">
    <h2 class="section-title">Late <b>Deals</b></h2>
    <div class="cards">
      <article class="card"><div class="photo" role="img" aria-label="Caravan lounge interior"></div><h3>The Birchwood</h3><dl><dt>Caravan type</dt><dd>Lodge</dd><dt>Sleeps</dt><dd>6</dd></dl><div class="more">From £199<em>More info</em></div></article>
      <article class="card"><div class="photo" role="img" aria-label="Lodge open plan living area"></div><h3>The Alder</h3><dl><dt>Caravan type</dt><dd>Lodge</dd><dt>Sleeps</dt><dd>4</dd></dl><div class="more">From £175<em>More info</em></div></article>
      <article class="card"><div class="photo" role="img" aria-label="Caravan bedroom"></div><h3>The Rowan</h3><dl><dt>Caravan type</dt><dd>Caravan</dd><dt>Sleeps</dt><dd>6</dd></dl><div class="more">From £150<em>More info</em></div></article>
      <article class="card"><div class="photo" role="img" aria-label="Lodge lounge with sofas"></div><h3>The Hazel</h3><dl><dt>Caravan type</dt><dd>Lodge</dd><dt>Sleeps</dt><dd>8</dd></dl><div class="more">From £260<em>More info</em></div></article>
      <article class="card"><div class="photo" role="img" aria-label="Caravan living room"></div><h3>The Larch</h3><dl><dt>Caravan type</dt><dd>Lodge</dd><dt>Sleeps</dt><dd>6</dd></dl><div class="more">From £199<em>More info</em></div></article>
    </div>
  </div>
</section>

<section class="feeds">
  <div class="wrap">
    <div class="col">
      <h4>Latest reviews</h4>
      <div class="item"><div class="who">Hannah Pellow <span>stayed in The Birchwood</span></div><div class="stars">★★★★★</div><p>A lovely lodge in a quiet spot. The children loved the pool and the woodland walks, and check in was quick and friendly. We will be back next summer.</p></div>
      <div class="item"><div class="who">Gemma Tresize <span>stayed in The Alder</span></div><div class="stars">★★★★★</div><p>Clean, warm and very well equipped caravan. Staff were helpful and the site was peaceful. A perfect short break for our whole family.</p></div>
    </div>
    <div class="col">
      <h4>Blog Feed</h4>
      <div class="item"><div class="who">New lodges arriving on site this spring</div><p>Three new family lodges with decking and garden views are being placed along the river path ready for the coming season.</p><div class="date">Posted on 12 March 2016</div></div>
      <div class="item"><div class="who">Summer events for the whole family</div><p>From bushcraft mornings to evening quiz nights, our summer events calendar is now open for guests to browse and book.</p><div class="date">Posted on 02 March 2016</div></div>
    </div>
    <aside class="social">
      <header>Social Feed</header>
      <div class="sub">Recent Activity</div>
      <ul>
        <li><i></i><div><b>Pinebrook Stays</b> shared a new photo of the lodge park in spring.</div></li>
        <li><i></i><div><b>Pinebrook Stays</b> posted late deals for the coming half term break.</div></li>
        <li><i></i><div><b>Pinebrook Stays</b> updated the availability dates for the summer.</div></li>
        <li><i></i><div><b>Pinebrook Stays</b> thanked guests for their kind reviews.</div></li>
      </ul>
    </aside>
  </div>
</section>

<footer class="footer">
  <div class="wrap">
    <div class="fcol first"><h5>Newsletter</h5>Sign up for our latest offers and news<div class="input">Enter email</div><span class="btn">Subscribe now</span></div>
    <div class="fcol"><h5>Contact us</h5>Pinebrook Stays, Hollow Lane,<br>Fernmoor, FM4 2PL<br>+44 1632 960 418<br>hello@pinebrookstays.com</div>
    <div class="fcol"><h5>Welcome</h5>Book a stay<br>News<br>Caravans &amp; Lodges<br>Site Facilities<br>Local Attractions</div>
    <div class="fcol"><h5>Information</h5>Frequently Asked<br>Local Attractions<br>Payment Plans<br>Contact Us<br>Terms and Conditions</div>
    <div class="fcol"><h5>Follow us</h5><div class="circle"><i></i>Community</div><div class="circle"><i></i>Updates</div><div class="circle"><i></i>Videos</div></div>
  </div>
</footer>
<div class="copy">Copyright © 2016 Pinebrook Stays. All rights reserved.</div>

</body>
</html>
```